Varnell Climate Business Card Design

Design new, 2 sides, business cards for a residential and light commercial heating, air conditioning contractor.

Target Market(s)

Homeowners, small businesses

Industry/Entity Type

Business

Contact Information for Business Card

Dominic Westerhall
Phone - 862-415-2736
Email
Address - PO box 518
Brightwater NJ 07912
Website - www.HarborBreezeLLC.example

Requirements
Must have
• logo, company colors, standard size with no die cut, so I can use nova stamp

```html
<!DOCTYPE html>
<html lang="en">
<head>
<meta charset="utf-8">
<title>Varnell Climate Business Cards</title>
<link rel="stylesheet" href="https://fonts.googleapis.com/css2?family=Alfa+Slab+One&family=Roboto:wght@400;500&display=swap">
<style>
  :root {
    --page: #e6e6e6;
    --card-red: #862a2c;
    --band-gold: #e2b112;
    --accent-orange: #e8861e;
    --name-yellow: #f5c518;
    --ink-dark: #6a1a1c;
    --text-light: #f3e9e4;
  }
  * { box-sizing: border-box; margin: 0; padding: 0; }
  html, body { width: 1200px; height: 576px; overflow: hidden; }
  body {
    background: var(--page);
    position: relative;
    font-family: "Roboto", Arial, sans-serif;
  }
  .card {
    position: absolute;
    background: var(--card-red);
    overflow: hidden;
    box-shadow: 0 3px 6px rgba(0,0,0,0.25);
  }
  .card--front { left: 81px; top: 138px; width: 485px; height: 294px; }
  .card--back { left: 602px; top: 138px; width: 482px; height: 292px; }

  .brand-name {
    position: absolute;
    font-family: "Alfa Slab One", Georgia, serif;
    font-weight: 400;
    color: var(--name-yellow);
    text-align: center;
    line-height: 1;
    white-space: nowrap;
  }
  .card--front .brand-name { left: 0; right: 0; top: 112px; font-size: 40px; }
  .card--back .brand-name { left: 264px; width: 200px; top: 200px; font-size: 24px; }

  .tagline-band {
    position: absolute;
    left: 0; right: 0; top: 249px; height: 22px;
    background: var(--band-gold);
    color: var(--ink-dark);
    font-size: 12.5px;
    line-height: 22px;
    text-align: center;
  }

  .accent-field {
    position: absolute;
    left: 0; top: 0; width: 482px; height: 130px;
    background: linear-gradient(100deg, rgba(232,134,30,0) 38%, rgba(232,134,30,0.55) 58%, var(--accent-orange) 75%);
  }

  .services {
    position: absolute;
    right: 30px; top: 18px;
    list-style: none;
    text-align: right;
    color: var(--ink-dark);
    font-size: 12px;
    font-weight: 500;
    line-height: 16px;
  }
  .services .chev { display: inline-block; width: 14px; text-align: right; }

  .person-name {
    position: absolute;
    left: 21px; top: 71px;
    font-family: "Alfa Slab One", Georgia, serif;
    font-size: 19px;
    color: var(--name-yellow);
  }
  .person-role {
    position: absolute;
    left: 21px; top: 98px;
    font-size: 11px;
    color: var(--text-light);
  }

  .contacts {
    position: absolute;
    left: 21px; top: 196px;
    list-style: none;
    color: var(--text-light);
    font-size: 13px;
    line-height: 17px;
  }
  .contacts li { display: flex; align-items: center; height: 17px; }
  .contacts svg { width: 12px; height: 12px; margin-right: 12px; fill: var(--name-yellow); }
</style>
</head>
<body>

<section class="card card--front" aria-label="Card front">
  <div class="brand-name">Varnell Climate</div>
  <div class="tagline-band">Residential &amp; Light Commercial Heating &nbsp;• Air Conditioning Contractor</div>
</section>

<section class="card card--back" aria-label="Card back">
  <div class="accent-field" role="img" aria-label="Warm orange decorative accent area"></div>

  <ul class="services">
    <li>Residential and Light<span class="chev">«</span></li>
    <li>Commercial Heating<span class="chev"></span></li>
    <li>Air Conditioning<span class="chev">«</span></li>
    <li>Contractor<span class="chev"></span></li>
  </ul>

  <div class="person-name">Dominic Westerhall</div>
  <div class="person-role">Managing Director</div>

  <ul class="contacts">
    <li><svg viewBox="0 0 12 12"><path d="M2,1 h2 l1,3 -1.5,1 a6,6 0 0 0 3.5,3.5 l1,-1.5 3,1 v2 a1,1 0 0 1 -1,1 A10,10 0 0 1 1,2 a1,1 0 0 1 1,-1z"/></svg>862-415-2736</li>
    <li><svg viewBox="0 0 12 12"><path d="M0,2 h12 v8 h-12z M0.8,2.8 l5.2,4 5.2,-4" stroke="var(--card-red)" stroke-width="0.9"/></svg>info@VarnellClimateLLC.example</li>
    <li><svg viewBox="0 0 12 12"><path d="M6,0 a4.3,4.3 0 0 1 4.3,4.3 c0,3 -4.3,7.7 -4.3,7.7 s-4.3,-4.7 -4.3,-7.7 A4.3,4.3 0 0 1 6,0z M6,2.6 a1.7,1.7 0 1 0 0.01,0z"/></svg>PO box 518 Brightwater NJ 07912</li>
    <li><svg viewBox="0 0 12 12"><circle cx="6" cy="6" r="5.5"/><path d="M0.5,6 h11 M6,0.5 v11 M6,0.5 c-3,3 -3,8 0,11 M6,0.5 c3,3 3,8 0,11" stroke="var(--card-red)" stroke-width="0.8" fill="none"/></svg>VarnellClimateLLC.example</li>
  </ul>

  <div class="brand-name">Varnell Climate</div>
</section>

</body>
</html>
```